Vindgerdi - Start-up company selling electricity

Hello let me tell you about Vindgerdi.

Vindgerdi is start-up company selling electricity in Iceland. The operations of the company consist of making power usage forecasts for our customers, purchasing the electricity wholesale from the energy producers, and selling the electricity to the consumer. We are focused on tech by using optimization and machine learning to minimize electricity prices to our customers. Our marketing strategy is to portray a tech company mindset and to show dedication to driving down the electricity price on the market.

We need your help to make our website pop. Possible concepts to work with are as follows:

- Iceland the land of ice and fire
- Green energy
- Innovation
- Tech and data science

Link to our website: https://prufa.vindgerdi-example.is/
We are open to ideas.
Thank you!

Target Market(s)

Electricity consumers both homes and companies.

Number of Pages Required

1 page

Font styles to use
Serif
Sans Serif

```html
<!DOCTYPE html>
<html lang="en">
<head>
<meta charset="utf-8">
<title>Vindgerdi – Electricity in Iceland</title>
<link rel="stylesheet" href="https://fonts.googleapis.com/css2?family=Lato:wght@400;700&family=Roboto:wght@400;500;700&display=swap">
<style>
:root{
  --navy:#0d1a3f;
  --navy-deep:#081231;
  --hero-a:#0a1f55;
  --hero-b:#06123a;
  --red:#9a1c1c;
  --red-btn:#b5211d;
  --text:#222;
  --white:#fff;
  --line:#c9ced9;
}
*{box-sizing:border-box;margin:0;padding:0}
html,body{width:1200px;height:3416px;overflow:hidden}
body{position:relative;background:var(--white);font-family:'Lato',sans-serif;color:var(--text)}
.abs{position:absolute}
.heading{font-family:'Roboto',sans-serif;font-weight:700;text-transform:uppercase}

/* header */
.site-header{left:0;top:0;width:1200px;height:73px;background:var(--white)}
.brand{left:111px;top:14px;display:flex;align-items:center;gap:12px;font-family:'Lato',sans-serif;font-weight:700;font-size:38px;color:var(--red);letter-spacing:1px}
.brand-dot{width:38px;height:38px;border-radius:50%;background:var(--navy)}
.main-nav{right:112px;top:27px;display:flex;gap:27px;font-size:16px;color:#333;text-transform:uppercase}
.main-nav span{font-weight:400}

/* hero */
.hero{left:0;top:73px;width:1200px;height:558px;background:radial-gradient(circle at 25% 40%,#12308a 0%,var(--hero-a) 35%,var(--hero-b) 100%)}
.hero-art{left:680px;top:0;width:380px;height:558px;background:radial-gradient(ellipse at 50% 65%,#39b8ff 0%,#1566c4 22%,rgba(10,40,110,0) 60%)}
.hero h1{left:111px;top:200px;font-size:38px;color:var(--white)}
.hero p{left:111px;top:262px;font-size:15px;font-weight:700;color:var(--white)}
.btn-outline{border:2px solid var(--white);border-radius:5px;color:var(--white);font-weight:700;font-size:16px;text-transform:uppercase;display:flex;align-items:center;justify-content:center}
.hero .btn-outline{left:110px;top:308px;width:133px;height:46px}

/* about */
.about-photo{left:111px;top:716px;width:566px;height:391px;background:radial-gradient(circle at 52% 55%,#ffd36a 0%,#e8731e 18%,#7a3a22 45%,#3b2a2e 100%)}
.about-card{left:523px;top:904px;width:565px;height:392px;background:linear-gradient(135deg,#0b1636,#0e1d44);color:var(--white);padding:28px 30px}
.about-card h2{font-size:26px;margin-bottom:16px}
.about-card h3{font-size:16px;font-weight:700;line-height:24px;text-transform:uppercase;margin-bottom:16px}
.about-card p{font-size:15px;line-height:24px}
.about-card .btn-outline{position:absolute;left:29px;top:312px;width:133px;height:46px}

/* future */
.future{left:0;top:1380px;width:600px;height:410px;background:linear-gradient(160deg,#16244f,var(--navy))}
.future h2{position:absolute;left:111px;top:130px;font-size:31px;color:var(--white)}
.future p{position:absolute;left:111px;top:180px;width:360px;font-size:15px;line-height:24px;color:var(--white)}
.future-photo{left:600px;top:1380px;width:600px;height:410px;background:linear-gradient(180deg,#3b6fa8 0%,#dfe4ea 28%,#7d8a94 48%,#5c4e48 70%,#8a5a4a 100%)}

/* prices */
.price-title{left:0;top:1866px;width:1200px;text-align:center;font-size:31px;color:#222}
.price-card{top:1933px;width:303px;height:340px;border:2px solid var(--red);border-radius:4px;text-align:center}
.price-icon{width:74px;height:74px;border-radius:50%;background:var(--navy);margin:29px auto 12px}
.price-value{font-family:'Roboto',sans-serif;font-weight:500;font-size:40px;color:var(--red)}
.price-unit{font-family:'Roboto',sans-serif;font-weight:500;font-size:26px;margin-top:4px}
.price-name{font-size:20px;margin-top:10px}
.btn-red-outline{width:240px;height:56px;margin:17px auto 0;border:2px solid var(--red);border-radius:6px;color:var(--red);font-weight:700;font-size:15px;display:flex;align-items:center;justify-content:center;text-transform:uppercase}

/* business */
.business{left:0;top:2361px;width:1200px;height:725px;background:linear-gradient(90deg,#06173a 0%,#0a2050 40%,#0b2252 100%)}
.business-art{left:0;top:0;width:520px;height:725px;background:radial-gradient(circle at 66% 52%,#6fdcff 0%,#1b78c8 12%,rgba(10,32,80,0) 50%)}
.business h2{position:absolute;left:524px;top:72px;width:564px;text-align:center;font-size:31px;color:var(--white)}
.tab{position:absolute;top:135px;width:125px;height:41px;border-radius:3px;display:flex;align-items:center;justify-content:center;font-size:17px;color:var(--white);text-transform:uppercase}
.tab-active{left:676px;background:var(--red-btn)}
.tab-idle{left:811px;border:2px solid var(--white)}
.field{position:absolute;height:46px;border:1px solid var(--line);border-radius:3px;color:var(--white);font-size:15px;padding:13px 17px}
.btn-send{position:absolute;left:709px;top:602px;width:194px;height:44px;background:var(--red-btn);border-radius:3px;color:var(--white);font-weight:700;font-size:14px;display:flex;align-items:center;justify-content:center;text-transform:uppercase}

/* footer */
.site-footer{left:0;top:3086px;width:1200px;height:330px;background:var(--navy-deep);color:var(--white)}
.footer-brand{position:absolute;left:111px;top:97px;display:flex;align-items:center;gap:12px;font-weight:700;font-size:38px;letter-spacing:1px}
.footer-brand .brand-dot{background:var(--white)}
.footer-col{position:absolute;top:68px;font-size:15px}
.footer-col h4{font-size:16px;font-weight:700;text-transform:uppercase;margin-bottom:14px}
.footer-col li{list-style:none;line-height:24px}
.contact-row{display:flex;align-items:center;gap:12px;line-height:24px;margin-bottom:7px}
.footer-rule{position:absolute;left:111px;top:220px;width:980px;height:1px;background:#3b4668}
.socials{position:absolute;left:535px;top:238px;display:flex;gap:12px}
.socials span{width:24px;height:24px;border-radius:50%;background:var(--white)}
.copyright{position:absolute;left:0;top:285px;width:1200px;text-align:center;font-size:15px}
</style>
</head>
<body>

<header class="abs site-header">
  <div class="abs brand"><span class="brand-dot"></span>VINDGERDI</div>
  <nav class="abs main-nav"><span>About Vindgerdi</span><span>Question &amp; Answer</span><span>Terms of Business</span></nav>
</header>

<section class="abs hero">
  <div class="abs hero-art" role="img" aria-label="Glowing wireframe light bulb made of connected network points"></div>
  <h1 class="abs heading">Welcome to Vindgerdi</h1>
  <p class="abs">Vindgerdi is start-up company selling electricity in Iceland.</p>
  <div class="abs btn-outline">Get Started</div>
</section>

<div class="abs about-photo" role="img" aria-label="Hands joining two gears against a sunset"></div>
<section class="abs about-card">
  <h2 class="heading">About Vindgerdi</h2>
  <h3>What is Vindgerdi's unique position in the electricity sales market?</h3>
  <p>Vindgerdi uses automation and artificial intelligence to achieve lower prices in the electricity market. Our goal is to minimize the cost of energy sales, promote energy balance and offer good service. Vindgerdi's goal is to offer its customers the most favorable electricity prices in Iceland. Electricity is part of the monthly costs of households and companies, and by doing business with Vindgerdi.</p>
  <div class="btn-outline">Learn More</div>
</section>

<section class="abs future">
  <h2 class="heading">The Future is Exciting</h2>
  <p>Let's make the electricity system smarter together. Vindgerdi uses artificial intelligence, data science and automation to minimize costs and promote eccentricity.</p>
</section>
<div class="abs future-photo" role="img" aria-label="Icelandic town with colourful roofs below a snow-covered mountain"></div>

<h2 class="abs heading price-title">Price List</h2>
<div class="abs price-card" style="left:280px">
  <div class="price-icon"></div>
  <div class="price-value">6.95</div>
  <div class="price-unit">ISK / KWH</div>
  <div class="price-name heading" style="font-weight:500">Electric Acceleration</div>
  <div class="btn-red-outline">Make a Price Comparison</div>
</div>
<div class="abs price-card" style="left:617px">
  <div class="price-icon"></div>
  <div class="price-value">6.22</div>
  <div class="price-unit">ISK / KWH</div>
  <div class="price-name heading" style="font-weight:500">Electric Acceleration</div>
  <div class="btn-red-outline">Make a Price Comparison</div>
</div>

<section class="abs business">
  <div class="abs business-art" role="img" aria-label="Hand touching a glowing digital network"></div>
  <h2 class="heading">Welcome to Business</h2>
  <div class="tab tab-active">Company</div>
  <div class="tab tab-idle">Home</div>
  <div class="field" style="left:524px;top:207px;width:275px">Company ID Number</div>
  <div class="field" style="left:811px;top:207px;width:277px">Company Name</div>
  <div class="field" style="left:524px;top:268px;width:275px">Address</div>
  <div class="field" style="left:811px;top:268px;width:277px">Postal code and place</div>
  <div class="field" style="left:524px;top:328px;width:275px">Company Contact</div>
  <div class="field" style="left:811px;top:328px;width:277px">Phone Number</div>
  <div class="field" style="left:524px;top:388px;width:564px">Email</div>
  <div class="field" style="left:524px;top:449px;width:564px;height:132px">Comments</div>
  <div class="btn-send">Send a Quote Request</div>
</section>

<footer class="abs site-footer">
  <div class="footer-brand"><span class="brand-dot"></span>VINDGERDI</div>
  <div class="footer-col" style="left:583px">
    <h4>Quick Link</h4>
    <ul><li>About Vindgerdi</li><li>Question &amp; Answer</li><li>Terms of business</li></ul>
  </div>
  <div class="footer-col" style="left:836px">
    <h4>Contact Us</h4>
    <div class="contact-row"><svg width="12" height="14" viewBox="0 0 12 14"><path d="M6 0a5 5 0 0 0-5 5c0 4 5 9 5 9s5-5 5-9a5 5 0 0 0-5-5zm0 7a2 2 0 1 1 0-4 2 2 0 0 1 0 4z" fill="#fff"/></svg>Hafnargata 8 220 Hafnarfjordur</div>
    <div class="contact-row"><svg width="14" height="11" viewBox="0 0 14 11"><rect x="0.75" y="0.75" width="12.5" height="9.5" fill="none" stroke="#fff" stroke-width="1.5"/><path d="M1 1l6 5 6-5" fill="none" stroke="#fff" stroke-width="1.5"/></svg>hallo@vindgerdi-example.is</div>
    <div class="contact-row"><svg width="13" height="13" viewBox="0 0 13 13"><path d="M3 0l2 3-1.5 1.5a8 8 0 0 0 5 5L10 8l3 2-1 3C5 13 0 8 0 1z" fill="#fff"/></svg>555-0199</div>
  </div>
  <div class="footer-rule"></div>
  <div class="socials"><span></span><span></span><span></span><span></span></div>
  <div class="copyright">© 2021 Vindgerdi. All Rights Reserved.</div>
</footer>

</body>
</html>
```